Harrow Grading LLC business card design

Excavation company business cards

Contact Information for Business Card

Harrow Grading LLC cell phone 208-417-6290 office phone 208-319-4856 harrowgradingllc@maplecove.com Driveways, site prep, retaining walls, septic systems, rock delivery

Colors

Designer to choose colors to be used in the design.

```html
<!DOCTYPE html>
<html lang="en">
<head>
<meta charset="UTF-8">
<title>Harrow Grading LLC — Business Cards</title>
<link rel="stylesheet" href="https://fonts.googleapis.com/css2?family=Arimo:wght@400;700&display=swap">
<style>
  :root {
    --orange: #e86e22;
    --grey: #7b7b7b;
    --white: #ffffff;
    --backdrop: #bdbdbd;
  }
  * { margin: 0; padding: 0; box-sizing: border-box; }
  html, body { width: 1200px; height: 800px; overflow: hidden; }
  body {
    background: var(--backdrop);
    font-family: "Arimo", Arial, sans-serif;
    display: flex;
    align-items: center;
    justify-content: center;
    gap: 40px;
  }
  .card {
    width: 540px;
    height: 309px;
    position: relative;
    overflow: hidden;
    box-shadow: 0 10px 24px rgba(0,0,0,0.25);
  }

  /* Front */
  .card-front { background: var(--orange); color: var(--white); }
  .front-art {
    position: absolute;
    top: 0; right: 0;
    width: 210px; height: 100%;
    background: linear-gradient(135deg, var(--white) 0%, var(--white) 45%, var(--grey) 46%, var(--grey) 100%);
    clip-path: polygon(35% 0, 100% 0, 100% 100%, 0 100%);
  }
  .front-info {
    position: absolute;
    left: 32px; top: 38px;
    width: 290px;
  }
  .brand-name {
    font-weight: 700;
    font-size: 22px;
    letter-spacing: 0.5px;
    text-transform: uppercase;
    display: flex;
    align-items: center;
    gap: 9px;
    white-space: nowrap;
  }
  .brand-mark {
    width: 16px; height: 16px;
    background: currentColor;
    display: inline-block;
    flex: none;
  }
  .person { margin-top: 42px; }
  .person-name { font-weight: 700; font-size: 20px; letter-spacing: 0.5px; }
  .person-role { font-size: 15px; margin-top: 3px; }
  .contacts { list-style: none; margin-top: 20px; }
  .contacts li {
    display: flex; align-items: center; gap: 9px;
    font-size: 14px; line-height: 23px;
    white-space: nowrap;
  }
  .contacts svg { width: 14px; height: 14px; flex: none; }

  /* Back */
  .card-back {
    background: var(--white);
    border-bottom: 4px solid var(--orange);
    color: var(--orange);
  }
  .back-brand {
    position: absolute;
    top: 118px; left: 0; right: 0;
    justify-content: center;
    font-size: 34px;
    letter-spacing: 1px;
  }
  .back-brand .brand-mark { width: 22px; height: 22px; }
  .services {
    position: absolute;
    bottom: 34px; left: 0; right: 0;
    text-align: center;
    font-size: 15px;
    color: var(--orange);
    white-space: nowrap;
  }
  .services span + span::before {
    content: "";
    display: inline-block;
    width: 6px; height: 6px;
    border-radius: 50%;
    background: var(--grey);
    margin: 0 8px 2px;
  }
</style>
</head>
<body>

<section class="card card-front">
  <div class="front-art" role="img" aria-label="Illustration of an excavator bucket with teeth, white and grey on orange"></div>
  <div class="front-info">
    <div class="brand-name"><span class="brand-mark"></span>Harrow Grading LLC</div>
    <div class="person">
      <div class="person-name">DANIEL BROOKS</div>
      <div class="person-role">Managing Director</div>
    </div>
    <ul class="contacts">
      <li>
        <svg viewBox="0 0 14 14" aria-hidden="true"><rect x="3.5" y="1" width="7" height="12" rx="1.2" fill="none" stroke="#fff" stroke-width="1.4"/><circle cx="7" cy="11" r="0.8" fill="#fff"/></svg>
        208-417-6290
      </li>
      <li>
        <svg viewBox="0 0 14 14" aria-hidden="true"><path d="M3 1.5l2.2 2.6-1.3 1.6c.8 1.7 2.1 3 3.8 3.8l1.6-1.3 2.6 2.2-1.4 1.9C6 12 2 8 1.2 3z" fill="#fff"/></svg>
        208-319-4856
      </li>
      <li>
        <svg viewBox="0 0 14 14" aria-hidden="true"><rect x="1" y="3" width="12" height="8.5" fill="#fff"/><path d="M1 3l6 5 6-5" fill="none" stroke="#e86e22" stroke-width="1.2"/></svg>
        harrowgradingllc@maplecove.com
      </li>
    </ul>
  </div>
</section>

<section class="card card-back">
  <div class="brand-name back-brand"><span class="brand-mark"></span>Harrow Grading LLC</div>
  <p class="services"><span>Driveways</span><span>Site prep</span><span>Retaining walls</span><span>Septic systems</span><span>Rock delivery</span></p>
</section>

</body>
</html>
```